We are a recruitment company based in Norwich/Cambridge England.
I have included our company logo which we want to remain the same.

What we are looking for is a new creative Business card which will really stand out!!

Contact Information for Business Card

Harriet Dunmore
email: Harriet@plavex.co.uk
Address: Brackwell House
Fenmoor Enterprise Park
Partridge Way
Norwich
QB9 3KX
Tel:01632 960418

```html
<!DOCTYPE html>
<html lang="en">
<head>
<meta charset="utf-8">
<title>Plavex Business Card</title>
<link rel="stylesheet" href="https://fonts.googleapis.com/css2?family=Jost:wght@400;500;600;700&display=swap">
<style>
  :root {
    --backdrop: #2a2a2a;
    --card: #2d2b2b;
    --card-mark: #3b3939;
    --white: #ffffff;
    --grey: #8a8a8d;
    --green: #7dc242;
    --shadow: rgba(0, 0, 0, 0.55);
  }
  * { box-sizing: border-box; margin: 0; padding: 0; }
  html, body {
    width: 1200px;
    height: 800px;
    overflow: hidden;
    background: var(--backdrop);
    font-family: "Jost", sans-serif;
  }
  .stage {
    width: 1200px;
    height: 800px;
    display: flex;
    flex-direction: column;
    align-items: center;
    justify-content: center;
    gap: 26px;
  }
  .card {
    position: relative;
    width: 630px;
    height: 360px;
    background: var(--card);
    box-shadow: 0 14px 30px var(--shadow);
    overflow: hidden;
  }
  .card-mark {
    position: absolute;
    width: 300px;
    height: 300px;
    border-radius: 50%;
    background: var(--card-mark);
  }
  .card--back .card-mark { right: 40px; top: 30px; }
  .card--front .card-mark { right: 36px; top: 30px; }

  /* Back */
  .back-brand {
    position: absolute;
    left: 34px;
    bottom: 30px;
    display: flex;
    align-items: center;
    gap: 12px;
  }
  .back-brand__dot {
    width: 34px;
    height: 34px;
    border-radius: 50%;
    background: var(--green);
  }
  .back-brand__name {
    font-size: 34px;
    font-weight: 500;
    color: var(--grey);
    line-height: 1;
  }

  /* Front */
  .front-brand {
    position: absolute;
    left: 36px;
    top: 34px;
  }
  .front-brand__name {
    font-size: 76px;
    font-weight: 600;
    color: var(--white);
    line-height: 0.95;
    letter-spacing: -1px;
  }
  .front-brand__tagline {
    margin-top: 6px;
    font-size: 13px;
    font-weight: 500;
    color: var(--white);
    letter-spacing: 5.2px;
  }
  .person {
    position: absolute;
    left: 36px;
    top: 170px;
  }
  .person__name {
    font-size: 32px;
    font-weight: 600;
    color: var(--grey);
    line-height: 1;
  }
  .person__role {
    margin-top: 4px;
    font-size: 17px;
    font-weight: 500;
    color: var(--green);
    letter-spacing: 0.5px;
  }
  .address {
    position: absolute;
    left: 36px;
    top: 240px;
    font-size: 14px;
    line-height: 1.3;
    color: var(--white);
  }
  .contacts {
    position: absolute;
    left: 36px;
    top: 284px;
    list-style: none;
  }
  .contacts__item {
    display: flex;
    align-items: center;
    gap: 10px;
    font-size: 16px;
    line-height: 22px;
    color: var(--white);
  }
  .contacts__icon { width: 14px; height: 14px; flex: none; }
  .contacts__accent { color: var(--green); }
</style>
</head>
<body>
<main class="stage">
  <section class="card card--back" aria-label="Card back">
    <div class="card-mark" aria-hidden="true"></div>
    <div class="back-brand">
      <span class="back-brand__dot" aria-hidden="true"></span>
      <span class="back-brand__name">Plavex</span>
    </div>
  </section>

  <section class="card card--front" aria-label="Card front">
    <div class="card-mark" aria-hidden="true"></div>
    <header class="front-brand">
      <div class="front-brand__name">Plavex</div>
      <div class="front-brand__tagline">Technology Recruitment</div>
    </header>
    <div class="person">
      <div class="person__name">Harriet Dunmore</div>
      <div class="person__role">CEO &amp; FOUNDER</div>
    </div>
    <address class="address" style="font-style:normal">
      Brackwell House Fenmoor Enterprise Park,<br>
      Partridge Way Norwich, QB9 3KX
    </address>
    <ul class="contacts">
      <li class="contacts__item">
        <svg class="contacts__icon" viewBox="0 0 14 14" aria-hidden="true"><path d="M3 1 L5 4 L4 5.5 Q5.5 8.5 8.5 10 L10 9 L13 11 L11.5 13 Q5 12.5 1 3 Z" fill="#7dc242"/></svg>
        01632 960418
      </li>
      <li class="contacts__item">
        <svg class="contacts__icon" viewBox="0 0 14 14" aria-hidden="true"><rect x="0.5" y="3" width="13" height="9" fill="#7dc242"/><path d="M0.5 3 L7 8 L13.5 3" fill="none" stroke="#2d2b2b" stroke-width="1.2"/></svg>
        Harriet@plavex.co.uk
      </li>
      <li class="contacts__item">
        <svg class="contacts__icon" viewBox="0 0 14 14" aria-hidden="true"><circle cx="8" cy="6" r="4.5" fill="none" stroke="#7dc242" stroke-width="1.8"/><path d="M4.8 9.2 L1.5 12.5" stroke="#7dc242" stroke-width="2"/></svg>
        <span>www.<span class="contacts__accent">plavex.co.uk</span></span>
      </li>
    </ul>
  </section>
</main>
</body>
</html>
```